Small Business Broker Business Card Design

A business card design for a small business brokerage, which is a financial service, not unlike real estate brokerage, but for small businesses such as laundromats, pizza shops, restaurants, cleaners etc. The designs should all be simple, more conservative in nature, using the colors and font of the logo. Again, think real estate Brokerage as a business context
Contact Information for Business Card
Name: Glen R. Harlow. Title: Small Business Advisor. Email: g.harlow@bayfieldcapitalworks.example. Mobile: (555) 274-3918. Office: (555) 806-2147. www.bayfieldcapitalworks.example

```html
<!DOCTYPE html>
<html lang="en">
<head>
<meta charset="utf-8">
<title>Bayfield Capital Works – Business Card</title>
<link href="https://fonts.googleapis.com/css2?family=Montserrat:wght@400;500;600;700;800&display=swap" rel="stylesheet">
<style>
  :root{
    --navy:#1d3a6b;
    --green:#8cc63f;
    --white:#ffffff;
    --ink:#1f2430;
    --stage:#e6e7ea;
  }
  *{box-sizing:border-box;margin:0;padding:0}
  html,body{width:1200px;height:800px;overflow:hidden}
  body{
    background:var(--stage);
    font-family:"Montserrat",sans-serif;
    display:flex;flex-direction:column;align-items:center;justify-content:center;gap:60px;
  }
  .card{
    position:relative;width:560px;height:320px;border-radius:18px;overflow:hidden;
    box-shadow:0 6px 18px rgba(0,0,0,.18);
  }
  /* back side */
  .card--back{background:var(--navy);display:flex;align-items:center;justify-content:center}
  .brand{display:flex;flex-direction:column;align-items:flex-start}
  .brand__row{display:flex;align-items:center;gap:12px}
  .brand__square{width:18px;height:18px;background:var(--green);flex:none}
  .brand__name{font-weight:700;text-transform:uppercase;letter-spacing:.04em;line-height:1.05}
  .brand__tagline{font-weight:600;text-transform:uppercase;color:var(--green);letter-spacing:.12em;line-height:1.35}
  .card--back .brand__name{color:var(--white);font-size:25px}
  .card--back .brand__tagline{font-size:10.5px;margin-top:7px;margin-left:30px}

  /* front side */
  .card--front{background:var(--white)}
  .wave{position:absolute;inset:0}
  .card--front .brand{position:absolute;left:28px;top:128px}
  .card--front .brand__name{color:var(--navy);font-size:16px}
  .card--front .brand__square{width:13px;height:13px}
  .card--front .brand__row{gap:8px}
  .card--front .brand__tagline{font-size:7px;margin-top:6px;margin-left:21px;letter-spacing:.1em}
  .divider{position:absolute;left:252px;top:50px;width:1px;height:140px;background:var(--navy)}
  .person{position:absolute;left:266px;top:46px}
  .person__name{color:var(--navy);font-weight:800;font-size:21px;line-height:1.1}
  .person__title{color:var(--ink);font-size:11.5px;font-weight:500;margin-top:2px}
  .contacts{position:absolute;left:266px;top:108px;list-style:none}
  .contacts__item{display:flex;align-items:center;gap:8px;color:var(--ink);font-size:11px;height:18px}
  .contacts__icon{width:11px;height:11px;flex:none}
</style>
</head>
<body>

<section class="card card--back" aria-label="Card back">
  <div class="brand">
    <div class="brand__row">
      <span class="brand__square"></span>
      <span class="brand__name">Bayfield Capital Works, Inc</span>
    </div>
    <span class="brand__tagline">Steady advice for every main street business deal</span>
  </div>
</section>

<section class="card card--front" aria-label="Card front">
  <svg class="wave" viewBox="0 0 560 320" aria-hidden="true">
    <path d="M100 320 C230 238 355 258 450 216 C512 190 546 150 560 100" fill="none" stroke="var(--green)" stroke-width="4" transform="translate(0,-9)"/>
    <path d="M110 320 C240 240 360 260 450 225 C510 200 545 160 560 110 L560 320 Z" fill="var(--navy)"/>
  </svg>

  <div class="brand">
    <div class="brand__row">
      <span class="brand__square"></span>
      <span class="brand__name">Bayfield Capital<br>Works, Inc</span>
    </div>
    <span class="brand__tagline">Steady advice for every<br>main street business deal</span>
  </div>

  <div class="divider"></div>

  <div class="person">
    <div class="person__name">Glen R. Harlow</div>
    <div class="person__title">Small Business Advisor</div>
  </div>

  <ul class="contacts">
    <li class="contacts__item">
      <svg class="contacts__icon" viewBox="0 0 12 12"><path d="M1 5 Q6 1 11 5 L9 6.5 L8 5 Q6 4.3 4 5 L3 6.5 Z M3 7 H9 L10 11 H2 Z" fill="var(--navy)"/></svg>
      (555) 806-2147
    </li>
    <li class="contacts__item">
      <svg class="contacts__icon" viewBox="0 0 12 12"><rect x="3" y="0.5" width="6" height="11" rx="1.2" fill="var(--navy)"/><rect x="4" y="2" width="4" height="6.5" fill="var(--white)"/></svg>
      (555) 274-3918
    </li>
    <li class="contacts__item">
      <svg class="contacts__icon" viewBox="0 0 12 12"><rect x="0.5" y="2.5" width="11" height="7.5" fill="var(--navy)"/><path d="M0.8 2.8 L6 7 L11.2 2.8" fill="none" stroke="var(--white)" stroke-width="1"/></svg>
      g.harlow@bayfieldcapitalworks.example
    </li>
    <li class="contacts__item">
      <svg class="contacts__icon" viewBox="0 0 12 12"><circle cx="6" cy="6" r="5.5" fill="var(--navy)"/><path d="M0.5 6 H11.5 M6 0.5 C3 3.5 3 8.5 6 11.5 M6 0.5 C9 3.5 9 8.5 6 11.5" fill="none" stroke="var(--white)" stroke-width=".8"/></svg>
      www.bayfieldcapitalworks.example
    </li>
  </ul>
</section>

</body>
</html>
```